2018 TVPAC Conference Theme Artwork

We need artwork designed around the theme of this year's human resources conference. The theme is "Celebrating 20 Years Together Towards Tomorrow". The artwork should be designed as a 4x6 postcard and will eventually be adapted/reformatted to use on the registration website, sales materials, e-newsletters, conference guide cover and signage.

Target Market(s)

Attendees are human resources professionals. Exhibitors and sponsors are companies who want to sell their products/services to human resource professionals

Colors

Designer to choose colors to be used in the design.

Requirements
Must have
• NO BORING PIXVAULT IMAGERY PLEASE.
• Theme: Celebrating 20 Years Together Towards Tomorrow
• Event: 20th Annual TVPA Conference
• Dates/Times: Tuesday, May 15, 2018, 12:30pm - 5:00pm and Wednesday, May 16, 2018 7:30am - 5:30pm
• Website: tvpaconference.example
• Location: The HALL at the Corvane Manchester
Nice to have
• Engaging, celebratory, visually attractive
Should not have
• NO BORING PIXVAULT IMAGERY.

```html
<!DOCTYPE html>
<html lang="en">
<head>
<meta charset="utf-8">
<title>TVPAC 2018 Conference Postcard</title>
<link rel="stylesheet" href="https://fonts.googleapis.com/css2?family=Roboto+Condensed:wght@300;700&display=swap">
<style>
  :root {
    --page-bg: #d9d9d9;
    --brand-blue: #064a86;
    --deep-navy: #0d2a3d;
    --ink: #1a1a1a;
    --white: #ffffff;
    --footer-light: #ffffff;
    --footer-grey: #e4e4e4;
  }
  html, body {
    margin: 0;
    padding: 0;
    width: 1200px;
    height: 1200px;
    overflow: hidden;
    background: var(--page-bg);
  }
  .postcard {
    position: absolute;
    left: 40px;
    top: 220px;
    width: 1120px;
    height: 760px;
    background: linear-gradient(90deg, var(--footer-grey) 0%, var(--footer-light) 55%, var(--footer-grey) 100%);
    box-shadow: 0 6px 18px rgba(0,0,0,0.25);
    overflow: hidden;
    font-family: "Roboto Condensed", "Arial Narrow", sans-serif;
  }
  .postcard-art {
    position: absolute;
    left: 0;
    top: 0;
  }
  .headline {
    position: absolute;
    right: 44px;
    margin: 0;
    color: var(--white);
    text-transform: uppercase;
    line-height: 1;
    white-space: nowrap;
    letter-spacing: -0.5px;
  }
  .headline--light { font-weight: 300; }
  .headline--bold { font-weight: 700; }
  .theme-celebrating { top: 46px; font-size: 58px; }
  .theme-years { top: 104px; font-size: 80px; }
  .theme-together { top: 188px; font-size: 62px; }
  .theme-tomorrow { top: 259px; font-size: 62px; }
  .event-annual { top: 383px; font-size: 62px; }
  .event-name { top: 456px; font-size: 66px; }

  .schedule {
    position: absolute;
    right: 44px;
    top: 556px;
    text-align: right;
    color: var(--ink);
    font-weight: 700;
    font-size: 29px;
    line-height: 36px;
    text-transform: uppercase;
  }
  .schedule-day { margin: 0 0 30px; }
  .schedule-day:last-child { margin-bottom: 0; }

  .organizer {
    position: absolute;
    left: 40px;
    top: 505px;
    color: var(--brand-blue);
    font-weight: 700;
    font-size: 34px;
    line-height: 36px;
    text-transform: uppercase;
    margin: 0;
  }
  .venue {
    position: absolute;
    left: 40px;
    top: 624px;
    display: flex;
    align-items: center;
    gap: 18px;
  }
  .venue-name {
    margin: 0;
    color: var(--ink);
    font-weight: 700;
    font-size: 30px;
    line-height: 36px;
    text-transform: uppercase;
  }
  .website {
    position: absolute;
    left: 40px;
    top: 706px;
    margin: 0;
    color: var(--brand-blue);
    font-weight: 700;
    font-size: 24px;
    line-height: 28px;
  }
</style>
</head>
<body>
  <main class="postcard">
    <svg class="postcard-art" width="1120" height="760" viewBox="0 0 1120 760">
      <defs>
        <linearGradient id="crowdTones" x1="0" y1="0" x2="1" y2="1">
          <stop offset="0" stop-color="#e8304f"/>
          <stop offset="0.25" stop-color="#f6a21c"/>
          <stop offset="0.5" stop-color="#27a9c5"/>
          <stop offset="0.75" stop-color="#7a3a8f"/>
          <stop offset="1" stop-color="#4bb04a"/>
        </linearGradient>
      </defs>
      <polygon class="crowd-illustration" role="img"
               aria-label="Colourful crowd of small people figures with a circular badge of two figures"
               points="0,0 564,0 414,475 0,475" fill="url(#crowdTones)"/>
      <polygon class="panel-shadow" points="345,475 414,475 395,527" fill="var(--deep-navy)"/>
      <polygon class="title-panel" points="560,0 1120,0 1120,527 395,527" fill="var(--brand-blue)"/>
      <g class="forward-arrow" transform="translate(375,156) rotate(-38)" fill="var(--deep-navy)">
        <polygon points="-120,-32 20,-32 20,-82 125,0 20,82 20,32 -120,32"/>
      </g>
    </svg>

    <p class="headline headline--light theme-celebrating">Celebrating</p>
    <p class="headline headline--light theme-years">20 Years</p>
    <p class="headline headline--bold theme-together">Together Towards</p>
    <p class="headline headline--bold theme-tomorrow">Tomorrow</p>
    <p class="headline headline--light event-annual">20th Annual</p>
    <h1 class="headline headline--bold event-name">TVPA Conference</h1>

    <p class="organizer">TVPA Regional<br>Council</p>

    <div class="venue">
      <svg class="venue-pin" width="60" height="60" viewBox="0 0 60 60" aria-hidden="true">
        <circle cx="30" cy="30" r="30" fill="var(--brand-blue)"/>
        <path d="M30 12c-7.2 0-13 5.6-13 12.6C17 34 30 48 30 48s13-14 13-23.4C43 17.6 37.2 12 30 12z" fill="var(--white)"/>
        <circle cx="30" cy="25" r="5" fill="var(--brand-blue)"/>
      </svg>
      <p class="venue-name">The Hall at the<br>Corvane Manchester</p>
    </div>

    <p class="website">tvpaconference.example</p>

    <div class="schedule">
      <p class="schedule-day">Tuesday, May 15, 2018<br>12:30PM - 5:00PM</p>
      <p class="schedule-day">Wednesday, May 16, 2018<br>7:30AM - 5:30PM</p>
    </div>
  </main>
</body>
</html>
```